I need a business card design for a new business based in South West Australia.
I specialize in residential window cleaning & general handyman maintenance.

Dale Marsh - 412 SILVER HAWK DETAILING
- Window Cleaning
- House Maintenance

```html
<!DOCTYPE html>
<html lang="en">
<head>
<meta charset="utf-8">
<title>412 Silver Hawk Detailing – Business Card</title>
<link href="https://fonts.googleapis.com/css2?family=Old+Standard+TT:wght@400;700&display=swap" rel="stylesheet">
<style>
  :root {
    --page-bg: #e9e6e1;
    --card-blue: #7fb8e0;
    --card-blue-light: #a9d3ef;
    --card-blue-deep: #5f9fd0;
    --frame-green: #8fb3a6;
    --frame-green-dark: #5f8578;
    --ink: #111418;
    --photo-white: #eef3f7;
    --photo-brown: #9a6e5c;
    --photo-sky: #8cc1e6;
  }
  * { box-sizing: border-box; margin: 0; padding: 0; }
  html, body {
    width: 1200px; height: 892px; overflow: hidden;
    background: var(--page-bg);
  }
  .canvas {
    width: 1200px; height: 892px;
    display: flex; align-items: center; justify-content: center;
  }
  .business-card {
    position: relative;
    width: 1000px; height: 572px;
    display: flex;
    background: var(--card-blue);
    box-shadow: 0 10px 30px rgba(0,0,0,0.18);
    overflow: hidden;
    font-family: "Old Standard TT", Georgia, serif;
    color: var(--ink);
  }
  .info-panel {
    position: relative;
    flex: 0 0 735px;
    background: linear-gradient(160deg, var(--card-blue-light) 0%, var(--card-blue) 55%, var(--card-blue-deep) 100%);
  }
  .house-artwork {
    position: absolute; inset: 0;
    background: radial-gradient(ellipse at 60% 60%, rgba(255,255,255,0.22), rgba(255,255,255,0) 65%);
  }
  .brand {
    position: absolute; left: 34px; top: 30px;
  }
  .company-name {
    font-size: 40px; font-weight: 700; letter-spacing: 1px;
    white-space: nowrap;
  }
  .tagline {
    margin-top: 6px; padding-left: 150px;
    font-size: 25px; line-height: 1.15;
  }
  .divider {
    position: absolute; left: 200px; top: 188px;
    width: 500px; height: 2px; background: var(--ink);
  }
  .contact-name {
    position: absolute; left: 212px; top: 250px;
    font-size: 54px; font-weight: 700;
  }
  .services {
    position: absolute; left: 300px; top: 360px;
    list-style: none; font-size: 30px; line-height: 1.6;
  }
  .window-frame {
    flex: 0 0 22px;
    background: linear-gradient(90deg, var(--frame-green-dark), var(--frame-green) 40%, var(--frame-green-dark));
  }
  .window-photo {
    flex: 1;
    background: linear-gradient(180deg, var(--photo-sky) 0%, var(--photo-white) 30%, var(--photo-brown) 55%, var(--photo-white) 75%, var(--photo-sky) 100%);
  }
</style>
</head>
<body>
<main class="canvas">
  <article class="business-card">
    <section class="info-panel">
      <div class="house-artwork" role="img" aria-label="Faint house outline with silhouettes of window cleaners at work"></div>
      <header class="brand">
        <h1 class="company-name">412 SILVER HAWK DETAILING</h1>
        <p class="tagline">residential window cleaning &amp;<br>general handyman maintenance</p>
      </header>
      <div class="divider"></div>
      <h2 class="contact-name">Dale Marsh</h2>
      <ul class="services">
        <li>Window Cleaning</li>
        <li>House Maintenance</li>
      </ul>
    </section>
    <div class="window-frame"></div>
    <div class="window-photo" role="img" aria-label="Photo of a soapy window pane being cleaned"></div>
  </article>
</main>
</body>
</html>
```